Website Redesign - We Need Your Magic!

Hello we are looking for you to help us re-design a high end and professional website for a high-end private school.

Here is the current site: http://www.ferndalecrest.com/

NOTE THIS IS DESIGN ONLY, NO CODING :)

The image they want to portray is that of high quality sports and education, in a creative "un-stiff" way.

Menu Bar: Horizontal

Look and Feel:

Site Colors: Dark green and a Gold yellow (logos are attached)

This site will represent a school so the look must be clean, bold, and classy. The site must have a very clean user interface, with things easily recognizable. Think simple.

The site should be visually appealing! If you come to me with templates, or a ton of text you will be out.

This site should be outside the box, we do not want boring, we do not want status quo. This site should instill excitement, innovation, and athletics.

So the main points again are:

1. High-end and classy look, with creative feel
2. Simple and clear navigation style
3. To cover the Junior and High School - Ferndale Crest College Schools

Think outside the box. We look forward to seeing what you come up with!!

Thank you for helping us create an amazing site for the school!

Industry/Entity Type

School

```html
<!DOCTYPE html>
<html lang="en">
<head>
<meta charset="utf-8">
<title>Ferndale Crest College</title>
<link href="https://fonts.googleapis.com/css2?family=Oswald:wght@400;500;600&family=Open+Sans:wght@400;600;700&display=swap" rel="stylesheet">
<style>
:root{
  --green-dark:#07401a;
  --green:#0b5124;
  --green-mid:#136b2f;
  --green-accent:#1a8a32;
  --gold:#ffe600;
  --ink:#1c1c1c;
  --text:#3a3a3a;
  --grey-row:#e4e4e4;
  --rule:#dcdcdc;
  --white:#ffffff;
}
*{box-sizing:border-box;margin:0;padding:0}
html,body{width:1200px;height:2796px;overflow:hidden}
body{position:relative;background:var(--white);font-family:"Open Sans",Arial,sans-serif;color:var(--text)}
.abs{position:absolute}
h2.section-title{font-family:"Oswald",Arial,sans-serif;font-weight:500;font-size:19px;color:var(--ink);text-transform:uppercase;white-space:nowrap}
h2.section-title span{color:var(--green-accent)}

/* header */
.site-header{left:0;top:0;width:1200px;height:121px;background:var(--green-dark)}
.brand{left:161px;top:40px;display:flex;align-items:center;gap:14px}
.brand-dot{width:40px;height:40px;border-radius:50%;background:var(--gold)}
.brand-name{font-family:"Oswald",Arial,sans-serif;font-weight:500;font-size:26px;color:var(--white);text-transform:uppercase;letter-spacing:.5px}
.info-call{left:652px;top:40px;display:flex;gap:10px;align-items:flex-start}
.info-call .label{font-family:"Oswald",Arial,sans-serif;font-size:12px;color:var(--white);text-transform:uppercase;letter-spacing:.3px}
.info-call .number{font-family:"Oswald",Arial,sans-serif;font-weight:500;font-size:23px;color:var(--gold);line-height:1.2}
.search{left:864px;top:40px}
.search .label{font-family:"Oswald",Arial,sans-serif;font-size:12px;color:var(--white);text-transform:uppercase;letter-spacing:.3px}
.search .field{margin-top:6px;width:176px;height:25px;background:var(--white);border-radius:2px;display:flex;align-items:center;justify-content:space-between;padding:0 7px;font-size:10px;color:#888}

/* nav */
.main-nav{left:0;top:121px;width:1200px;height:42px;background:linear-gradient(var(--green-mid),var(--green))}
.main-nav ul{list-style:none;display:flex;position:absolute;left:170px;top:0;height:42px}
.main-nav li{font-family:"Oswald",Arial,sans-serif;font-size:14px;color:var(--white);text-transform:uppercase;line-height:42px;padding:0 26px;letter-spacing:.3px;white-space:nowrap}
.main-nav li.active{background:var(--green-dark)}

/* hero */
.hero{left:0;top:163px;width:1200px;height:482px;background:linear-gradient(180deg,#c9d67a 0%,#9fb944 40%,#6f9a23 75%,#4d7c17 100%)}
.hero-arrow{top:370px}

/* welcome */
.welcome{left:161px;top:683px;width:650px}
.welcome p{font-size:12.5px;line-height:22px;margin-top:16px;color:var(--text)}
.social-feed{left:836px;top:683px;width:203px}
.feed-box{margin-top:18px;border:1px solid #cfd4da;height:130px;padding:8px;background:#fafafa}
.feed-head{display:flex;gap:8px;align-items:center}
.feed-head .sq{width:26px;height:26px;background:var(--green-accent)}
.feed-head .name{font-size:10px;font-weight:600;color:var(--green)}
.feed-box .likes{font-size:8px;color:#666;margin-top:6px}
.feed-grid{display:grid;grid-template-columns:repeat(4,36px);gap:5px;margin-top:5px}
.feed-grid div{height:28px;background:#b9bcc2}
.feed-box .foot{font-size:7px;color:#888;margin-top:6px}

.rule{height:1px;background:var(--rule);left:161px;width:878px}

/* notes */
.note{top:1013px;width:420px}
.note .body{display:flex;gap:22px;margin-top:26px}
.note .photo{width:149px;height:149px;flex:none}
.note p{font-size:11.5px;line-height:21px}
.read-more{display:inline-block;margin-top:14px;border:1px solid var(--green-accent);font-size:10.5px;color:var(--green);padding:3px 7px}
.note-divider{left:601px;top:1075px;width:1px;height:215px;background:var(--rule)}

/* calendar */
.calendar{left:161px;top:1380px;width:878px}
.cal-table{margin-top:30px;width:878px;border-collapse:collapse}
.cal-table th{font-family:"Oswald",Arial,sans-serif;font-weight:400;font-size:15px;color:var(--green-accent);text-transform:uppercase;height:40px}
.cal-table td{font-size:10.5px;text-align:center;line-height:15px;height:52px;color:#222}
.cal-table td.term-label{text-align:left;padding-left:8px;font-family:"Oswald",Arial,sans-serif;font-size:14px;text-transform:uppercase;width:232px}
.cal-table tr.shade td{background:var(--grey-row)}

/* download band */
.download-band{left:161px;top:1792px;width:878px;height:107px;background:var(--green);display:flex;justify-content:center;align-items:center;gap:28px}
.gold-btn{width:278px;height:46px;background:var(--gold);font-family:"Oswald",Arial,sans-serif;font-size:14px;text-transform:uppercase;color:var(--ink);display:flex;align-items:center;justify-content:center;box-shadow:0 5px 0 rgba(0,0,0,.35)}

/* events */
.events{left:161px;top:1945px;width:652px}
.event-grid{display:flex;gap:24px;margin-top:24px}
.event{width:202px}
.event .photo{height:135px}
.event .date{font-family:"Oswald",Arial,sans-serif;font-size:15px;color:var(--ink);margin-top:12px;text-transform:uppercase}
.event .caption{font-size:11px;margin-top:6px}
.sports{left:836px;top:1945px;width:203px}
.sports ul{list-style:none;margin-top:24px}
.sports li{font-size:11px;line-height:31px}

/* partners */
.partner{top:2283px;width:152px;height:89px;background:var(--white);box-shadow:0 1px 4px rgba(0,0,0,.25);display:flex;align-items:center;justify-content:center}
.partner .mark{width:96px;height:40px;border-radius:6px}

/* footer */
.site-footer{left:0;top:2423px;width:1200px;height:373px;background:var(--green)}
.touch{left:161px;top:2495px}
.touch h2{color:var(--white)}
.touch h2 span{color:var(--gold)}
.contact-item{position:absolute;display:flex;gap:14px;width:280px}
.contact-item .ico{width:22px;height:22px;border:1px solid var(--gold);border-radius:50%;flex:none;display:flex;align-items:center;justify-content:center}
.contact-item .t{font-size:10.5px;color:var(--white);line-height:15px}
.contact-item .t b{display:block;color:var(--gold);font-weight:600;text-transform:uppercase}
.signup{left:757px;top:2410px;width:282px;height:316px;background:var(--green-mid);padding:48px 26px 0}
.signup-tab{left:757px;top:2398px;width:0;height:0;border-left:12px solid transparent;border-bottom:12px solid var(--green-mid)}
.signup h2{color:var(--white)}
.signup h2 span{color:var(--gold)}
.signup p{font-size:10.5px;color:var(--white);line-height:18px;margin-top:16px}
.signup .input{height:31px;background:var(--white);font-size:10px;color:#666;padding:0 9px;display:flex;align-items:center;margin-top:11px;width:232px}
.signup .btns{display:flex;gap:14px;margin-top:22px}
.signup .btn{height:30px;font-family:"Oswald",Arial,sans-serif;font-size:13px;text-transform:uppercase;display:flex;align-items:center;justify-content:center;width:109px}
.btn-sub{background:var(--gold);color:var(--ink)}
.btn-unsub{background:var(--green-dark);color:var(--white)}
.copy-bar{left:0;top:2745px;width:1200px;height:51px;background:var(--green-dark)}
.copy-bar .txt{position:absolute;left:161px;top:18px;font-size:10px;color:var(--white)}
.socials{position:absolute;left:966px;top:16px;display:flex;gap:6px}
.socials span{width:20px;height:20px;border-radius:50%;background:var(--gold)}
</style>
</head>
<body>

<header class="site-header abs">
  <div class="brand abs"><span class="brand-dot"></span><span class="brand-name">Ferndale Crest College</span></div>
  <div class="info-call abs">
    <svg width="20" height="24" viewBox="0 0 20 24"><rect x="1" y="1" width="18" height="22" rx="2" fill="#fff"/><rect x="4" y="4" width="12" height="7" fill="#07401a"/><g fill="#07401a"><rect x="4" y="13" width="3" height="2"/><rect x="9" y="13" width="3" height="2"/><rect x="4" y="17" width="3" height="2"/><rect x="9" y="17" width="3" height="2"/></g></svg>
    <div><div class="label">Information Call</div><div class="number">0771 482 905</div></div>
  </div>
  <div class="search abs">
    <div class="label">Search Now!</div>
    <div class="field"><span>Enter Your Keyword...</span>
      <svg width="10" height="10" viewBox="0 0 10 10"><circle cx="4" cy="4" r="3" fill="none" stroke="#888" stroke-width="1.3"/><line x1="6.2" y1="6.2" x2="9" y2="9" stroke="#888" stroke-width="1.3"/></svg>
    </div>
  </div>
</header>

<nav class="main-nav abs">
  <ul>
    <li class="active">Home</li><li>About</li><li>Academics</li><li>Sports</li><li>Joining Ferndale Crest</li><li>Working at the College</li><li>Contact</li>
  </ul>
</nav>

<section class="hero abs" role="img" aria-label="Five smiling children lying side by side on a sunny lawn"></section>
<svg class="hero-arrow abs" style="left:62px" width="30" height="56" viewBox="0 0 30 56"><polyline points="26,4 4,28 26,52" fill="none" stroke="#111" stroke-width="3"/></svg>
<svg class="hero-arrow abs" style="left:1108px" width="30" height="56" viewBox="0 0 30 56"><polyline points="4,4 26,28 4,52" fill="none" stroke="#111" stroke-width="3"/></svg>

<section class="welcome abs">
  <h2 class="section-title">Welcome to <span>Ferndale Crest College</span></h2>
  <p>Welcome to Ferndale Crest Group of Schools where our School Motto is 'Tabetana' meaning Togetherness. We aim to work together in every aspect of School life, from academics to sport. Ferndale Crest College opened on 14th February 1983 and occupies 120 ha of land amidst the low hills of the Marlow Hills, 8km west of Kestrelton. This location encourages focus on School life away from the distractions and hustle and bustle of the larger towns.</p>
  <p>The day scholars have the option of selected bus drop off points for parents to collect day scholars closer to home. Ferndale Crest College offers a wide range of academic subjects alongside a varied sport and extra-curricular program.</p>
</section>

<aside class="social-feed abs">
  <h2 class="section-title">Social <span>Feeds</span></h2>
  <div class="feed-box">
    <div class="feed-head"><span class="sq"></span><span class="name">Ferndale Crest School</span></div>
    <div class="likes">1,379 people follow Ferndale Crest School</div>
    <div class="feed-grid"><div></div><div></div><div></div><div></div><div></div><div></div><div></div><div></div></div>
    <div class="foot">Community feed panel</div>
  </div>
</aside>

<div class="rule abs" style="top:975px"></div>

<section class="note abs" style="left:161px">
  <h2 class="section-title">Headmaster's <span>Welcome Note</span></h2>
  <div class="body">
    <div class="photo" role="img" aria-label="Portrait of the headmaster" style="background:linear-gradient(#9aa3a8,#6b7a55)"></div>
    <div>
      <p>Welcome to Ferndale Crest College. Here at the College we aim to encourage each pupil to be a self-confident, well-rounded individual. We aim to propel them to the highest level of achievement in both academics and extra-curricular activities to provide them with the life skills they will need when they leave the College and to prepare them to be of value to society.</p>
      <span class="read-more">Read More</span>
    </div>
  </div>
</section>
<div class="note-divider abs"></div>
<section class="note abs" style="left:625px">
  <h2 class="section-title">Memorial Garden <span>Opened Speech Day 2011</span></h2>
  <div class="body">
    <div class="photo" role="img" aria-label="Students gathered at the memorial garden" style="background:linear-gradient(#5a6b3a,#3d4a2a)"></div>
    <div>
      <p>Every year the Lower Sixes choose a fundraising project - something for the community like a local orphanage or a local retirement home and then also do something to uplift the school. To uplift the school, the Lower Six Class of 2010 decided that they would like to honour and remember people who played a part in the development of the school.</p>
      <span class="read-more">Read More</span>
    </div>
  </div>
</section>

<div class="rule abs" style="top:1333px"></div>

<section class="calendar abs">
  <h2 class="section-title">School <span>Calender</span></h2>
  <table class="cal-table">
    <tr><th></th><th>First Term</th><th>Second Term</th><th>Third Term</th></tr>
    <tr class="shade"><td class="term-label">Begins</td><td>Tuesday 14th January</td><td>Tuesday 13th May</td><td>Tuesday 9th September</td></tr>
    <tr><td class="term-label">1st Fixture Free</td><td>Friday 31st January –<br>Monday 3rd February</td><td>Friday 30th May –<br>Monday 2nd June</td><td>Friday 26th September –<br>Monday 29th September</td></tr>
    <tr class="shade"><td class="term-label">Half-Term</td><td>Thursday 20th February –<br>Tuesday 25th February</td><td>Thursday 26th June –<br>Tuesday 1st July</td><td>Thursday 16th October –<br>Tuesday 21st October</td></tr>
    <tr><td class="term-label">2nd Fixture Free</td><td>Friday 14th March –<br>Monday 17th March</td><td>Friday 18th July –<br>Monday 21st July</td><td>Friday 7th November –<br>Monday 10th November</td></tr>
    <tr class="shade"><td class="term-label">Term Ends</td><td>Thursday 10th April</td><td>Friday 7th August</td><td>Thursday 4th December</td></tr>
  </table>
</section>

<section class="download-band abs">
  <span class="gold-btn">Download Registration Form</span>
  <span class="gold-btn">2nd Term 2014 Termly Calendar</span>
</section>

<section class="events abs">
  <h2 class="section-title">Upcoming <span>Events</span></h2>
  <div class="event-grid">
    <div class="event"><div class="photo" role="img" aria-label="Students playing basketball on an outdoor court" style="background:linear-gradient(#a86a4a,#6e5a4a)"></div><div class="date">Fri 25 July 2014</div><div class="caption">Basketball Regional Top Schools</div></div>
    <div class="event"><div class="photo" role="img" aria-label="Pupils performing on a school field" style="background:linear-gradient(#7a8a4a,#5a6a3a)"></div><div class="date">Sat 02 Aug 2013</div><div class="caption">School Play - Public Performance</div></div>
    <div class="event"><div class="photo" role="img" aria-label="Parents and pupils at an outdoor consultation" style="background:linear-gradient(#8a6a3a,#4a3a2a)"></div><div class="date">Thurs 07 Aug 2013</div><div class="caption">Consultation for 4B, 5B, L6, U6</div></div>
  </div>
</section>

<aside class="sports abs">
  <h2 class="section-title">Sports <span>Announcements</span></h2>
  <ul><li>- Rugby</li><li>- Hockey Boys</li><li>- Soccer</li><li>- Hockey Girls</li><li>- Basketball Girls</li></ul>
</aside>

<div class="rule abs" style="top:2237px"></div>

<div class="partner abs" style="left:186px"><span class="mark" style="background:#1f3f8f"></span></div>
<div class="partner abs" style="left:412px"><span class="mark" style="background:#e08a1e"></span></div>
<div class="partner abs" style="left:636px"><span class="mark" style="background:#f2b51a"></span></div>
<div class="partner abs" style="left:862px"><span class="mark" style="background:#e0561e"></span></div>

<footer class="site-footer abs"></footer>
<section class="touch abs">
  <h2 class="section-title">Get in <span>Touch</span></h2>
</section>
<div class="contact-item" style="left:161px;top:2556px">
  <span class="ico"><svg width="10" height="12" viewBox="0 0 10 12"><path d="M5 0a4 4 0 0 1 4 4c0 3-4 8-4 8S1 7 1 4a4 4 0 0 1 4-4z" fill="#ffe600"/><circle cx="5" cy="4" r="1.5" fill="#0b5124"/></svg></span>
  <div class="t"><b>Ferndale Crest College</b>Lorem ipsum dolor amet<br>dosis latrs us 256894</div>
</div>
<div class="contact-item" style="left:470px;top:2556px">
  <span class="ico"><svg width="10" height="12" viewBox="0 0 10 12"><path d="M5 0a4 4 0 0 1 4 4c0 3-4 8-4 8S1 7 1 4a4 4 0 0 1 4-4z" fill="#ffe600"/><circle cx="5" cy="4" r="1.5" fill="#0b5124"/></svg></span>
  <div class="t"><b>Map</b>Click here to see directions</div>
</div>
<div class="contact-item" style="left:161px;top:2672px">
  <span class="ico"><svg width="11" height="11" viewBox="0 0 11 11"><path d="M2 0h2l1 3-1.5 1a6 6 0 0 0 3.5 3.5L8 6l3 1v2a2 2 0 0 1-2 2A9 9 0 0 1 0 2a2 2 0 0 1 2-2z" fill="#ffe600"/></svg></span>
  <div class="t"><b>Phone Number</b>0771 306 214 / 0771 482 905</div>
</div>
<div class="contact-item" style="left:470px;top:2672px">
  <span class="ico"><svg width="12" height="9" viewBox="0 0 12 9"><rect x=".5" y=".5" width="11" height="8" fill="none" stroke="#ffe600"/><polyline points=".5,.5 6,5 11.5,.5" fill="none" stroke="#ffe600"/></svg></span>
  <div class="t"><b>Email Us</b>admin@ferndalecrest.com</div>
</div>

<div class="signup-tab abs"></div>
<section class="signup abs">
  <h2 class="section-title">Signup <span>Newsletter</span></h2>
  <p>If you would like to be added to the list of parents that receive the School Newsletter, please enter your details below.</p>
  <div class="input">Enter Your Name</div>
  <div class="input">Enter Your Email</div>
  <div class="btns"><span class="btn btn-sub">Subscribe</span><span class="btn btn-unsub">Unsubscribe</span></div>
</section>

<div class="copy-bar abs">
  <span class="txt">2014 Ferndale Crest College. All Rights Reserved.</span>
  <div class="socials"><span></span><span></span><span></span></div>
</div>

</body>
</html>
```